Corvane Capital Business Cards

These are professional business cards that are for my family office.
Put fake emails and phone numbers as of now until I finalize those components. This family office controls my families investments, assets, and future. The cards should be professional.
..
.
.
.
I just uploaded another variation of a logo I would like to see as a business card to I am inbeteen which logo to use

Target Market(s)

business

Industry/Entity Type

business

Contact Information for Business Card

Professional, wealth related, finance related.

Requirements
Must have
• Logo

```html
<!DOCTYPE html>
<html lang="en">
<head>
<meta charset="utf-8">
<title>Corvane Capital Business Cards</title>
<link rel="stylesheet" href="https://fonts.googleapis.com/css2?family=Playfair+Display:wght@400;600&family=Arimo:wght@400&display=swap">
<style>
  :root {
    --backdrop: #d4d4d4;
    --card: #262627;
    --gold: #b59a5e;
    --ink-light: #f2f2f2;
    --emboss: #48484b;
  }
  * { margin: 0; padding: 0; box-sizing: border-box; }
  html, body { width: 1200px; height: 788px; overflow: hidden; }
  body {
    background: var(--backdrop);
    display: flex;
    align-items: center;
    justify-content: center;
    gap: 40px;
  }
  .card {
    width: 540px;
    height: 309px;
    background: var(--card);
    border-radius: 22px;
    position: relative;
    overflow: hidden;
    box-shadow: 0 14px 30px rgba(0,0,0,0.25);
  }
  .card-front { display: flex; }
  .brand-panel {
    width: 250px;
    display: flex;
    align-items: center;
    justify-content: center;
    gap: 10px;
    padding-top: 70px;
  }
  .brand-square {
    width: 12px; height: 12px;
    background: var(--gold);
  }
  .brand-name {
    font-family: "Playfair Display", serif;
    font-weight: 400;
    font-size: 22px;
    letter-spacing: 1.5px;
    color: var(--ink-light);
    text-transform: uppercase;
  }
  .divider {
    width: 1px;
    height: 150px;
    background: var(--gold);
    align-self: center;
    margin-top: 60px;
  }
  .contact-panel {
    flex: 1;
    padding: 70px 0 0 26px;
    font-family: "Arimo", sans-serif;
    color: var(--ink-light);
    font-size: 14px;
    line-height: 1.3;
  }
  .person-name {
    font-family: "Playfair Display", serif;
    font-weight: 600;
    color: var(--gold);
    font-size: 19px;
    letter-spacing: 1px;
    text-transform: uppercase;
  }
  .person-title { margin-bottom: 12px; }
  .address { margin-bottom: 10px; }
  .contact-list { list-style: none; }
  .contact-list li { display: flex; align-items: center; gap: 8px; }
  .contact-list svg { width: 11px; height: 11px; fill: var(--gold); flex: none; }
  .card-back {
    display: flex;
    align-items: center;
    justify-content: center;
  }
  .back-name {
    font-family: "Playfair Display", serif;
    font-weight: 400;
    font-size: 44px;
    letter-spacing: 3px;
    color: var(--emboss);
    text-transform: uppercase;
  }
</style>
</head>
<body>
  <section class="card card-front">
    <div class="brand-panel">
      <span class="brand-square"></span>
      <span class="brand-name">Corvane Capital</span>
    </div>
    <div class="divider"></div>
    <div class="contact-panel">
      <p class="person-name">Daniel Reyes</p>
      <p class="person-title">CEO/Founder</p>
      <p class="address">4820 Linden Park Rd Suite 200<br>Fairhaven, AB 857300</p>
      <ul class="contact-list">
        <li>
          <svg viewBox="0 0 12 12" aria-hidden="true"><path d="M2 1h3l1 3-2 1a7 7 0 0 0 3 3l1-2 3 1v3c0 1-1 1-1 1C5 11 1 7 1 2c0 0 0-1 1-1z"/></svg>
          (555) 318-4420
        </li>
        <li>
          <svg viewBox="0 0 12 12" aria-hidden="true"><path d="M1 2h10v8H1z M1 2l5 4 5-4" stroke="#262627" stroke-width="1"/></svg>
          DanielR@corvanecapital.com
        </li>
        <li>
          <svg viewBox="0 0 12 12" aria-hidden="true"><circle cx="6" cy="6" r="5"/><path d="M1 6h10M6 1v10" stroke="#262627" stroke-width="0.8"/></svg>
          www.corvanecapital.com
        </li>
      </ul>
    </div>
  </section>
  <section class="card card-back">
    <span class="back-name">Corvane Capital</span>
  </section>
</body>
</html>
```